Wholesale food company needs a package for Carp boilies (fishing)

We need a (5kg) doypack with handle design for a new brand here in the BENELUX called Tolvo Lures. We already have a logo but we need a flashing design to promote it on shows and webshops. The design must also include some transparant places so you can see the product inside. We have added the logo and the website is www.tolvolures.nl. You can look for an impression at http://marwick-goods.nl/product-category/baits/specials/

Target Market(s)

Carpf fishing and coarse angling

Industry/Entity Type

It Company

Requirements
Must have
• A slogan that suits both types of fishing.
• Extra information doypack:
• Material: PET/PE
• Thickness: 12µ/120µ
• Size: B 320 x H 450 MM

```html
<!DOCTYPE html>
<html lang="en">
<head>
<meta charset="utf-8">
<title>Tolvo Lures – Doypack Front and Back</title>
<link rel="stylesheet" href="https://fonts.googleapis.com/css2?family=Stardos+Stencil:wght@700&family=Arimo:wght@400;700&display=swap">
<style>
  :root {
    --page: #ffffff;
    --frame: #c8c8c8;
    --dim-label: #c4c4c4;
    --blue-dark: #2f55a4;
    --blue-mid: #3f86cf;
    --blue-light: #56c1ee;
    --green: #8cc63f;
    --boilie-light: #5ef06a;
    --boilie-dark: #1a9a2c;
    --ink: #231f20;
    --white: #ffffff;
  }
  * { margin: 0; padding: 0; box-sizing: border-box; }
  html, body { width: 1200px; height: 892px; overflow: hidden; background: var(--page); }
  .sheet {
    position: relative; width: 1200px; height: 892px;
    border: 1px solid var(--frame); background: var(--page);
    font-family: "Arimo", Arial, sans-serif;
  }
  .pack { position: absolute; top: 0; }
  .pack--front { left: 0; }
  .pack--back { left: 630px; }
  .dim { fill: var(--dim-label); font-family: "Arimo", Arial, sans-serif; font-size: 24px; }
  .brand { font-family: "Stardos Stencil", Impact, sans-serif; font-weight: 700; }
  .brand--title { font-size: 52px; letter-spacing: 1px; }
  .brand--sub { font-size: 34px; letter-spacing: 1px; }
  .fill-white { fill: var(--white); }
  .fill-blue { fill: var(--blue-dark); }
  .fill-green { fill: var(--green); }
  .tagline { fill: var(--white); font-weight: 700; font-size: 16.5px; }
  .ingredients { fill: var(--ink); font-size: 17px; }
  .website { fill: var(--ink); font-weight: 700; font-size: 22px; }
  .badge-name { fill: var(--blue-dark); font-family: "Stardos Stencil", Impact, sans-serif; font-weight: 700; font-size: 24px; }
</style>
</head>
<body>
<div class="sheet">

  <!-- Front panel -->
  <svg class="pack pack--front" width="600" height="892" viewBox="0 0 600 892">
    <defs>
      <linearGradient id="front-header" x1="0" y1="0" x2="1" y2="1">
        <stop offset="0" stop-color="var(--blue-light)"/>
        <stop offset="1" stop-color="var(--blue-dark)"/>
      </linearGradient>
      <linearGradient id="front-panel" x1="0" y1="0" x2="1" y2="1">
        <stop offset="0" stop-color="var(--blue-mid)"/>
        <stop offset="1" stop-color="var(--blue-dark)"/>
      </linearGradient>
      <radialGradient id="front-boilies" cx="0.5" cy="0.5" r="0.7">
        <stop offset="0" stop-color="var(--boilie-light)"/>
        <stop offset="1" stop-color="var(--boilie-dark)"/>
      </radialGradient>
    </defs>

    <text class="dim" x="26" y="118" transform="rotate(-90 26 118)">70mm</text>
    <text class="dim" x="26" y="490" transform="rotate(-90 26 490)">450mm</text>
    <text class="dim" x="246" y="882">320mm</text>
    <text class="dim" x="408" y="882">font</text>

    <path class="header" d="M40 130 V90 Q40 25 105 25 H482 Q547 25 547 90 V130 Z" fill="url(#front-header)"/>
    <rect class="handle-hole fill-white" x="188" y="58" width="212" height="54" rx="27"/>

    <rect class="body fill-white" x="40" y="130" width="507" height="715"/>
    <polygon class="panel-blue" points="40,130 547,130 547,700 425,388 40,250" fill="url(#front-panel)"/>
    <polygon class="band-green" points="40,148 425,385 40,212"/>
    <polygon class="band-green fill-green" points="40,150 422,386 40,212"/>
    <polygon class="band-light" points="40,250 422,390 40,300" fill="var(--blue-light)"/>
    <polygon class="stripe-blue fill-blue" points="432,398 547,650 547,720"/>
    <polygon class="stripe-green fill-green" points="418,392 547,700 547,760 526,716"/>

    <polygon class="boilies" role="img" aria-label="Photo of green boilies visible through the window"
      points="40,318 415,396 527,716 280,716 40,768" fill="url(#front-boilies)"/>

    <polygon class="band-green fill-green" points="280,730 547,760 547,790 260,744"/>
    <polygon class="band-light" points="255,740 547,800 547,812 240,752" fill="var(--blue-light)"/>
    <polygon class="stripe-blue fill-blue" points="440,760 547,770 547,845 520,845"/>
    <polygon class="band-green fill-green" points="40,790 180,740 200,748 40,820"/>
    <polygon class="band-light" points="40,830 190,752 205,758 60,845 40,845" fill="var(--blue-light)"/>

    <circle class="badge" cx="205" cy="690" r="86" fill="var(--white)" stroke="var(--green)" stroke-width="5"/>
    <text class="badge-name" x="205" y="699" text-anchor="middle">Tolvo Lures</text>

    <text class="brand brand--title fill-white" x="508" y="196" text-anchor="end">TOLVO LURES</text>
    <text class="brand brand--sub fill-white" x="510" y="240" text-anchor="end">CARP PRODUCTS</text>
    <text class="tagline" x="510" y="277" text-anchor="end">Eco Friendly</text>
    <text class="tagline" x="510" y="299" text-anchor="end">Premium Quality</text>
    <text class="tagline" x="510" y="321" text-anchor="end">100% Fresh</text>
    <text class="tagline" x="510" y="343" text-anchor="end">High Attraction</text>

    <text class="website" x="294" y="817" text-anchor="middle">www.tolvolures.nl</text>
  </svg>

  <!-- Back panel -->
  <svg class="pack pack--back" width="570" height="892" viewBox="630 0 570 892">
    <defs>
      <linearGradient id="back-header" x1="0" y1="0" x2="1" y2="1">
        <stop offset="0" stop-color="var(--blue-light)"/>
        <stop offset="1" stop-color="var(--blue-dark)"/>
      </linearGradient>
      <radialGradient id="back-boilies" cx="0.4" cy="0.4" r="0.8">
        <stop offset="0" stop-color="var(--boilie-light)"/>
        <stop offset="1" stop-color="var(--boilie-dark)"/>
      </radialGradient>
      <linearGradient id="back-stripe" x1="0" y1="0" x2="1" y2="0">
        <stop offset="0" stop-color="var(--blue-light)"/>
        <stop offset="1" stop-color="var(--blue-dark)"/>
      </linearGradient>
    </defs>

    <text class="dim" x="658" y="118" transform="rotate(-90 658 118)">70mm</text>
    <text class="dim" x="878" y="882">320mm</text>
    <text class="dim" x="1092" y="882">back</text>

    <path class="header" d="M670 130 V90 Q670 25 735 25 H1112 Q1177 25 1177 90 V130 Z" fill="url(#back-header)"/>
    <rect class="handle-hole fill-white" x="820" y="58" width="210" height="54" rx="27"/>

    <rect class="body fill-white" x="670" y="130" width="507" height="715"/>

    <polygon class="boilies" role="img" aria-label="Photo of green boilies visible through the window"
      points="670,130 1177,130 1177,140 790,390 670,560" fill="url(#back-boilies)"/>
    <polygon class="stripe-blue" points="1177,150 1177,220 800,395 790,392" fill="url(#back-stripe)"/>
    <polygon class="stripe-green fill-green" points="1177,235 1177,305 808,400"/>
    <polygon class="stripe-blue" points="785,395 670,570 670,760 760,470" fill="url(#back-stripe)"/>
    <polygon class="stripe-green fill-green" points="790,400 670,700 670,760"/>

    <polygon class="band-light" points="670,720 950,715 950,740 670,800" fill="url(#back-stripe)"/>
    <polygon class="band-green fill-green" points="670,800 980,740 1177,800 1177,835 1060,790 670,845"/>
    <polygon class="stripe-blue fill-blue" points="1080,740 1177,775 1177,820"/>

    <circle class="badge" cx="1010" cy="680" r="86" fill="var(--white)" stroke="var(--green)" stroke-width="5"/>
    <text class="badge-name" x="1010" y="689" text-anchor="middle">Tolvo Lures</text>

    <text class="brand brand--title fill-blue" x="805" y="440">TOLVO LURES</text>
    <text class="brand brand--sub fill-green" x="805" y="482">CARP PRODUCTS</text>
    <text class="ingredients" x="805" y="524">here ingredients lable come.</text>

    <text class="website" x="925" y="827" text-anchor="middle">www.tolvolures.nl</text>
  </svg>

</div>
</body>
</html>
```